Professional violinist needs business cards

I am trying to attract the following jobs:
-private violin lessons (primarily classical)
-performance gigs (weddings, birthday parties, funerals, etc.)
-collaborations with other artists (studio recordings, performances)

I want to communicate that I have a very high standard of excellence for my work, but I also love people and celebrations.
Values/style words I like are:
love, joy, peace, fun, beauty, authenticity, excellence, warmth, refined/sleek, free spirited. If that's too confusing, just ignore :)

I will attach my favorite business card template that I could find on Canva. The lines are supposed to be like a music staff, which I think is really cool, but I also don't want it to look too busy. I like the simple black and white--I think it looks sharp--but I also am open to other ideas. I also have seen business cards with pictures included that looked great, so I attached an image that could be used as well.

I am also attaching a file that I made of my initials that could be used as a logo, but I'm not sure if it should be included.

Information on the card:
-My name (18 letters total)
-"violinist"
-phone number, email, website

Thank you!

```html
<!DOCTYPE html>
<html lang="en">
<head>
<meta charset="UTF-8">
<title>Caroline Whitfield – Business Cards</title>
<link href="https://fonts.googleapis.com/css2?family=Barlow:wght@400;500&family=Barlow+Condensed:wght@400;500;600&display=swap" rel="stylesheet">
<style>
  :root {
    --backdrop: #e4dfd8;
    --card-white: #fbfbfb;
    --card-black: #050505;
    --ink: #1a1a1a;
    --ink-soft: #3a3a3a;
    --silver-light: #d9d9dc;
    --silver-dark: #8d8c92;
    --photo-light: #cfcfcf;
    --photo-mid: #8a8a8a;
    --photo-dark: #2b2b2b;
  }
  * { box-sizing: border-box; margin: 0; padding: 0; }
  html, body {
    width: 1200px; height: 1200px; overflow: hidden;
    background: var(--backdrop);
  }
  .canvas {
    width: 1200px; height: 1200px;
    display: flex; flex-direction: column;
    align-items: center; justify-content: center;
    gap: 56px;
  }
  .card {
    width: 900px; height: 514px;
    position: relative; overflow: hidden;
    box-shadow: 0 6px 18px rgba(0,0,0,0.18);
  }

  /* Back of card */
  .card--back {
    background: var(--card-black);
    display: flex; align-items: center; justify-content: center;
  }
  .brand-name {
    font-family: "Barlow Condensed", sans-serif;
    font-weight: 500;
    font-size: 64px;
    letter-spacing: 0.04em;
    color: var(--silver-light);
    text-transform: uppercase;
  }

  /* Front of card */
  .card--front { background: var(--card-white); }
  .card__photo {
    position: absolute; top: 0; right: 0;
    width: 500px; height: 100%;
    background:
      linear-gradient(90deg, var(--card-white) 0%, rgba(251,251,251,0) 30%),
      linear-gradient(160deg, var(--photo-light) 0%, var(--photo-mid) 45%, var(--photo-dark) 100%);
  }
  .card__info {
    position: absolute; left: 96px; top: 118px;
    color: var(--ink);
  }
  .name {
    font-family: "Barlow Condensed", sans-serif;
    font-size: 42px; line-height: 1;
    text-transform: uppercase;
    letter-spacing: 0.01em;
  }
  .name__first { font-weight: 600; }
  .name__last { font-weight: 400; }
  .role {
    margin-top: 10px;
    font-family: "Barlow", sans-serif;
    font-weight: 400; font-size: 19px;
    letter-spacing: 0.38em;
    color: var(--ink-soft);
    text-transform: uppercase;
  }
  .contact-list {
    list-style: none;
    margin-top: 74px;
    margin-left: 44px;
    display: flex; flex-direction: column; gap: 22px;
  }
  .contact-item {
    display: flex; align-items: center; gap: 22px;
    font-family: "Barlow", sans-serif;
    font-weight: 500; font-size: 27px;
    color: var(--ink);
  }
  .contact-item svg { width: 28px; height: 28px; flex-shrink: 0; }
</style>
</head>
<body>
<main class="canvas">

  <section class="card card--back" aria-label="Card back">
    <span class="brand-name">Caroline Whitfield</span>
  </section>

  <section class="card card--front" aria-label="Card front">
    <div class="card__photo" role="img" aria-label="Black and white photo of the violinist holding her violin and bow beside a stone wall"></div>

    <div class="card__info">
      <h1 class="name"><span class="name__first">Caroline</span> <span class="name__last">Whitfield</span></h1>
      <p class="role">Violinist</p>

      <ul class="contact-list">
        <li class="contact-item">
          <svg viewBox="0 0 24 24" aria-hidden="true"><path fill="currentColor" d="M6.6 2.5l3 3.4-1.8 2.3c1.1 2.6 3.4 5 6.1 6.2l2.2-1.9 3.4 3-1.7 3.1c-.4.6-1.1.9-1.8.8C9 18.4 4.8 13.8 3.8 6.6c-.1-.7.3-1.4.9-1.7z"/></svg>
          <span>(555) 218 - 0473</span>
        </li>
        <li class="contact-item">
          <svg viewBox="0 0 24 24" aria-hidden="true"><rect x="2" y="5" width="20" height="14" fill="currentColor"/><path d="M2.5 5.5L12 13l9.5-7.5M2.5 18.5l7-6.5M21.5 18.5l-7-6.5" stroke="#fbfbfb" stroke-width="1.4" fill="none"/></svg>
          <span>carolinewhitfield@mailbox.com</span>
        </li>
        <li class="contact-item">
          <svg viewBox="0 0 24 24" aria-hidden="true"><circle cx="12" cy="12" r="10" fill="currentColor"/><g stroke="#fbfbfb" stroke-width="1.2" fill="none"><ellipse cx="12" cy="12" rx="4.5" ry="10"/><path d="M2 12h20M3.5 7h17M3.5 17h17M12 2v20"/></g></svg>
          <span>www.carolinewhitfield.com</span>
        </li>
      </ul>
    </div>
  </section>

</main>
</body>
</html>
```